Ledgers On Track Business Card Design

We are a bookkeeping and accounting practice and are particularly passionate about Vantu as 'state of the art' accounting software. We offer a number of services which are listed on the back of the card. The logos for LOT have already been developed. There are also other logos of organisations we are involved with - Vantu (both certified advisor and silver partner), QAG, and filenow hub. Regarding colours, we would like to use the colours similar to our website, www.ledgersontrack.com, and these connect with the www.vantu.com.au website. The proposed layout as it is just does not look too great - it looks like an amateur has done it - which is true!

Industry/Entity Type

Accounting

Contact Information for Business Card

The details to appear on the card are found on the files uploaded. I have front and back rough layouts.

```html
<!DOCTYPE html>
<html lang="en">
<head>
<meta charset="utf-8">
<title>Ledgers On Track – Business Card</title>
<link rel="stylesheet" href="https://fonts.googleapis.com/css2?family=Bitter:wght@400;600;700&display=swap">
<style>
  :root {
    --bg: #ecebe7;
    --card: #ffffff;
    --blue: #4a5e9e;
    --green: #5aaa3c;
    --text: #2b2b2b;
    --grey: #7a7a7a;
    --badge: #b4b4b4;
    --badge-dark: #8c9aa3;
    --qag: #e07a3a;
  }
  * { box-sizing: border-box; margin: 0; padding: 0; }
  html, body { width: 1200px; height: 1023px; overflow: hidden; }
  body { background: var(--bg); font-family: "Bitter", Georgia, serif; color: var(--text); position: relative; }

  .card { position: absolute; width: 720px; height: 412px; background: var(--card);
    box-shadow: 0 6px 18px rgba(0,0,0,.18); overflow: hidden; }
  .card__band { position: absolute; left: 0; right: 0; bottom: 0; background: var(--green); }

  .brand-name { color: var(--blue); font-weight: 700; line-height: 1.05; }
  .brand-dot { border-radius: 50%; background: var(--green); flex: none; }

  .partner-mark { display: flex; align-items: center; gap: 10px; color: var(--blue); font-weight: 600; }
  .partner-dot { border-radius: 50%; background: var(--blue); flex: none; }
  .badge { border-radius: 50%; flex: none; }
  .badge--silver { background: var(--badge); }
  .badge--advisor { background: var(--badge-dark); }

  .assoc { display: flex; align-items: center; gap: 10px; color: var(--grey); }
  .assoc-dot { border-radius: 50%; background: var(--qag); flex: none; }

  /* back */
  .card--back { left: 80px; top: 60px; }
  .card--back .card__band { height: 16px; }
  .back__brand { position: absolute; left: 40px; top: 70px; width: 240px; font-size: 30px;
    display: flex; align-items: center; gap: 12px; }
  .back__brand .brand-dot { width: 40px; height: 40px; }
  .back__partners { position: absolute; left: 40px; top: 176px; display: flex; align-items: center; gap: 18px; }
  .back__partners .partner-mark { font-size: 28px; }
  .back__partners .partner-dot { width: 20px; height: 20px; }
  .back__partners .badge { width: 80px; height: 80px; }
  .back__qag { position: absolute; left: 40px; top: 280px; font-size: 24px; }
  .back__qag .assoc-dot { width: 26px; height: 26px; }
  .back__filenow { position: absolute; left: 40px; top: 328px; color: var(--blue); font-weight: 700; font-size: 28px; }
  .divider { position: absolute; left: 290px; top: 56px; width: 2px; height: 300px; background: var(--green); }
  .services { position: absolute; left: 318px; top: 70px; list-style: none; font-size: 16px; line-height: 1.25; }
  .services li { display: flex; gap: 10px; margin-bottom: 8px; margin-left: calc(var(--i) * 6px); }
  .services svg { flex: none; margin-top: 3px; }
  .service-title { color: var(--green); font-weight: 600; }

  /* front */
  .card--front { left: 400px; top: 540px; }
  .card--front .card__band { height: 56px; color: #fff; font-size: 17px; display: flex;
    align-items: center; justify-content: center; }
  .front__brand { position: absolute; left: 40px; top: 54px; font-size: 54px; display: flex; align-items: center; gap: 18px; }
  .front__brand .brand-dot { width: 60px; height: 60px; }
  .front__qag { position: absolute; left: 62px; top: 180px; font-size: 28px; }
  .front__qag .assoc-dot { width: 36px; height: 36px; }
  .contacts { position: absolute; left: 72px; top: 238px; list-style: none; font-size: 16px; line-height: 22px; }
  .contacts li { display: flex; align-items: center; gap: 12px; }
  .ico { width: 16px; height: 16px; border-radius: 3px; background: var(--green); flex: none; }
  .person { position: absolute; right: 60px; top: 170px; width: 260px; text-align: center; }
  .person__name { color: var(--green); font-size: 30px; font-weight: 600; }
  .person__role { color: var(--grey); font-size: 16px; line-height: 1.3; margin-top: 4px; }
  .front__partners { position: absolute; right: 66px; top: 264px; display: flex; align-items: center; gap: 16px; }
  .front__partners .partner-mark { font-size: 26px; }
  .front__partners .partner-dot { width: 18px; height: 18px; }
  .front__partners .badge { width: 70px; height: 70px; }
</style>
</head>
<body>

<section class="card card--back" aria-label="Card back">
  <div class="back__brand brand-name"><span class="brand-dot"></span>Ledgers On Track</div>
  <div class="back__partners">
    <div class="partner-mark"><span class="partner-dot"></span>Vantu</div>
    <div class="badge badge--silver" role="img" aria-label="Silver partner badge"></div>
  </div>
  <div class="assoc back__qag"><span class="assoc-dot"></span>QAG</div>
  <div class="back__filenow">filenow hub</div>
  <div class="divider"></div>
  <ul class="services">
    <li style="--i:0"><svg width="16" height="14" viewBox="0 0 16 14"><path d="M1 8l4 4 10-11" fill="none" stroke="#5aaa3c" stroke-width="3"/></svg><span><span class="service-title">Bookkeeping</span> - data entry,<br>bank reconciliation and review</span></li>
    <li style="--i:1"><svg width="16" height="14" viewBox="0 0 16 14"><path d="M1 8l4 4 10-11" fill="none" stroke="#5aaa3c" stroke-width="3"/></svg><span><span class="service-title">Payroll</span> - Vantu Payroll Specialist</span></li>
    <li style="--i:2"><svg width="16" height="14" viewBox="0 0 16 14"><path d="M1 8l4 4 10-11" fill="none" stroke="#5aaa3c" stroke-width="3"/></svg><span><span class="service-title">BAS</span> - QAG Public BAS Practitioner</span></li>
    <li style="--i:3"><svg width="16" height="14" viewBox="0 0 16 14"><path d="M1 8l4 4 10-11" fill="none" stroke="#5aaa3c" stroke-width="3"/></svg><span><span class="service-title">Training &amp; support</span> - Vantu Certified<br>Advisor</span></li>
    <li style="--i:4"><svg width="16" height="14" viewBox="0 0 16 14"><path d="M1 8l4 4 10-11" fill="none" stroke="#5aaa3c" stroke-width="3"/></svg><span class="service-title">Management reports</span></li>
    <li style="--i:5"><svg width="16" height="14" viewBox="0 0 16 14"><path d="M1 8l4 4 10-11" fill="none" stroke="#5aaa3c" stroke-width="3"/></svg><span><span class="service-title">Tax</span> - filenow hub Member</span></li>
    <li style="--i:6"><svg width="16" height="14" viewBox="0 0 16 14"><path d="M1 8l4 4 10-11" fill="none" stroke="#5aaa3c" stroke-width="3"/></svg><span class="service-title">HR services</span></li>
  </ul>
  <div class="card__band"></div>
</section>

<section class="card card--front" aria-label="Card front">
  <div class="front__brand brand-name"><span class="brand-dot"></span>Ledgers On Track</div>
  <div class="assoc front__qag"><span class="assoc-dot"></span>QAG</div>
  <ul class="contacts">
    <li><span class="ico"></span>03 9000 4821</li>
    <li><span class="ico"></span>0400 000 512</li>
    <li><span class="ico"></span>martin@ledgersontrack.com</li>
    <li><span class="ico"></span>www.ledgersontrack.com</li>
    <li>ABN 12 345 678 901</li>
  </ul>
  <div class="person">
    <div class="person__name">Martin Hale</div>
    <div class="person__role">B Comm MA PhD AQAG<br>Registered BAS agent</div>
  </div>
  <div class="front__partners">
    <div class="partner-mark"><span class="partner-dot"></span>Vantu</div>
    <div class="badge badge--advisor" role="img" aria-label="Certified advisor badge"></div>
  </div>
  <div class="card__band">12 Wattle Grove Road, Eltham VIC 3095</div>
</section>

</body>
</html>
```